Brake Test Training for Coal Mining

We offer Brake Test Training for Coal Mine workers. It's a legislative requirement that workers who are tasked with performing brake testing have certain competencies to do so. We test Light Vehicles and trailers, Heavy Vehicles and Mobile Mining Equipment like Graders, Scrapers and Dump Trucks.

```html
<!DOCTYPE html>
<html lang="en">
<head>
<meta charset="utf-8">
<title>Brake Test Training for Coal Mine Workers</title>
<link rel="stylesheet" href="https://fonts.googleapis.com/css2?family=Montserrat:wght@600&family=Roboto+Condensed:wght@700&display=swap">
<style>
  :root {
    --ink-black: #000000;
    --mine-yellow: #f8c620;
    --navy: #233576;
    --bright-blue: #2b4aa6;
    --paper: #ffffff;
    --stage: #eceef1;
    --rock-light: #cbbdb0;
    --rock-dark: #a89888;
    --machine-yellow: #dcb02c;
  }
  html, body {
    margin: 0;
    padding: 0;
    width: 1027px;
    height: 1200px;
    overflow: hidden;
    background: var(--stage);
  }
  .canvas {
    width: 1027px;
    height: 1200px;
    display: flex;
    align-items: center;
    justify-content: center;
  }
  .billboard {
    display: block;
    width: 1027px;
    height: 512.6px;
  }
  .headline {
    font-family: "Roboto Condensed", "Arial Narrow", sans-serif;
    font-weight: 700;
    font-size: 150px;
    fill: var(--mine-yellow);
  }
  .subhead {
    font-family: "Montserrat", Arial, sans-serif;
    font-weight: 600;
    font-size: 104px;
    fill: var(--paper);
  }
  .list-title,
  .list-item {
    font-family: "Roboto Condensed", "Arial Narrow", sans-serif;
    font-weight: 700;
    font-size: 47px;
    fill: var(--navy);
  }
  .bullet { fill: var(--mine-yellow); }
  .phone-number {
    font-family: "Roboto Condensed", "Arial Narrow", sans-serif;
    font-weight: 700;
    font-size: 122px;
    fill: var(--navy);
  }
  .phone-badge { fill: var(--mine-yellow); }
  .phone-glyph { fill: var(--navy); }
  .brand-name {
    font-family: "Roboto Condensed", "Arial Narrow", sans-serif;
    font-weight: 700;
    font-size: 50px;
    fill: var(--navy);
  }
  .brand-dot { fill: var(--navy); }
</style>
</head>
<body>
<main class="canvas">
  <svg class="billboard" viewBox="0 0 1773 885" xmlns="http://www.w3.org/2000/svg" aria-labelledby="billboard-title">
    <title id="billboard-title">Brake Test Training for Coal Mine workers</title>
    <defs>
      <linearGradient id="photo-tone" x1="0" y1="0" x2="0.6" y2="1">
        <stop offset="0" stop-color="var(--rock-light)"/>
        <stop offset="0.35" stop-color="var(--rock-dark)"/>
        <stop offset="0.55" stop-color="var(--machine-yellow)"/>
        <stop offset="1" stop-color="#c9a43a"/>
      </linearGradient>
    </defs>

    <rect class="panel-base" x="0" y="0" width="1773" height="885" fill="var(--paper)"/>

    <!-- equipment photo area -->
    <polygon class="equipment-photo" role="img" aria-label="Photo of a large yellow wheel loader filling a haul truck in an open-cut quarry"
      points="0,0 515,0 408,332 1080,332 1080,760 300,760 215,885 0,885" fill="url(#photo-tone)"/>

    <!-- headline band -->
    <polygon class="headline-band" points="515,0 1773,0 1773,210 450,210" fill="var(--ink-black)"/>
    <!-- subhead band -->
    <polygon class="subhead-band" points="450,210 1773,210 1773,332 408,332" fill="var(--navy)"/>
    <polygon class="subhead-accent" points="450,210 522,210 470,332 408,332" fill="var(--bright-blue)"/>

    <!-- bottom-left diagonal rule -->
    <polygon class="corner-rule" points="308,760 326,760 241,885 223,885" fill="var(--navy)"/>

    <!-- headline text -->
    <text class="headline" x="1705" y="157" text-anchor="end" textLength="1095" lengthAdjust="spacingAndGlyphs">Brake Test Training</text>
    <text class="subhead" x="1702" y="302" text-anchor="end" textLength="1090" lengthAdjust="spacingAndGlyphs">for Coal Mine workers</text>

    <!-- equipment list -->
    <g class="equipment-list">
      <text class="list-title" x="1175" y="395">We test</text>
      <circle class="bullet" cx="1196" cy="440" r="13"/>
      <text class="list-item" x="1230" y="457">Light Vehicles and trailers,</text>
      <circle class="bullet" cx="1196" cy="497" r="13"/>
      <text class="list-item" x="1230" y="514">Heavy Vehicles,</text>
      <circle class="bullet" cx="1196" cy="555" r="13"/>
      <text class="list-item" x="1230" y="572">Mobile Mining Equipment</text>
      <circle class="bullet" cx="1196" cy="612" r="13"/>
      <text class="list-item" x="1230" y="629">Graders, Scrapers,</text>
      <circle class="bullet" cx="1196" cy="668" r="13"/>
      <text class="list-item" x="1230" y="685">Dump Trucks</text>
    </g>

    <!-- phone -->
    <g class="contact-phone">
      <circle class="phone-badge" cx="380" cy="808" r="46"/>
      <path class="phone-glyph" d="M362,782 l12,-4 l10,20 l-9,7 c4,10 10,16 20,20 l7,-9 l20,10 l-4,12 c-3,7 -10,8 -17,6 c-22,-7 -38,-23 -45,-45 c-2,-7 -1,-14 6,-17 z"/>
      <text class="phone-number" x="455" y="847" textLength="630" lengthAdjust="spacingAndGlyphs">1300 555 018</text>
    </g>

    <!-- brand -->
    <g class="brand">
      <circle class="brand-dot" cx="1215" cy="810" r="14"/>
      <text class="brand-name" x="1245" y="828">Summit Operator Training</text>
    </g>
  </svg>
</main>
</body>
</html>
```